Flat Belly Design Graphics for Social

I want to create 9 social media graphics (new Instagram size 4:5 (1080 x 1350 pixels) focusing on our Flat Belly Graphics, using the pics attached. Use the attached pics, NO RANDOM STOCK PHOTOGRAPHY. For the color scheme of the graphics, the color palette is attached. YOU MUST POST ALL 9 GRAPHICS IN ONE ENTRY.
Using the 3 titles below, create one set of graphics. 1) with all text, then for the others, use the pictures as detailed below in IMPORTANT:
1. Ten-Week Bright Morning Reboot
2. The Quick Garden Kitchen Menu Guide
3. Studio Habits for Lasting Energy Past Midlife - Zero Gym Needed
IMPORTANT:
Only use RK Pic 1 and RK Pic 2 with the title, Ten-Week Bright Morning Reboot
Only use meal plan1 and meal plan2 pics with the title, Quick Garden Kitchen Menu Guide
Only use studio habits 1 and studio habits 2 pics with the title, Studio Habits for Lasting Energy Past Midlife - Zero Gym Needed
women over 40

```html
<!DOCTYPE html>
<html lang="en">
<head>
<meta charset="utf-8">
<title>Morning Reboot Social Set</title>
<link href="https://fonts.googleapis.com/css2?family=Oswald:wght@300;500;700&display=swap" rel="stylesheet">
<style>
:root{
  --backdrop:#1c0209;
  --blush:#f9d7e2;
  --rose:#e299b0;
  --pale:#fbeef0;
  --forest:#2d4a45;
  --ink:#111111;
  --white:#ffffff;
  --photo-warm:#c9a48e;
  --photo-food:#6b4a36;
}
html,body{margin:0;padding:0;width:1074px;height:1200px;overflow:hidden;background:var(--backdrop);}
.canvas{position:relative;width:1074px;height:1200px;}
.post{position:absolute;width:259px;height:324px;overflow:hidden;}
.post svg{display:block;width:100%;height:100%;}
.col-a{left:122px}.col-b{left:405px}.col-b-alt{left:407px}.col-c{left:684px}
.row-1{top:94px}.row-2{top:438px}.row-3{top:782px}
.head{font-family:"Oswald",sans-serif;font-weight:700;}
.mid{font-family:"Oswald",sans-serif;font-weight:500;}
.light{font-family:"Oswald",sans-serif;font-weight:300;}
.fill-white{fill:var(--white)}.fill-forest{fill:var(--forest)}.fill-ink{fill:var(--ink)}
</style>
</head>
<body>
<div class="canvas">

  <svg width="0" height="0" style="position:absolute">
    <defs>
      <pattern id="dot-grid" width="14" height="14" patternUnits="userSpaceOnUse">
        <circle cx="3" cy="3" r="2.4" fill="#e299b0"/>
      </pattern>
      <linearGradient id="photo-person" x1="0" y1="0" x2="0" y2="1">
        <stop offset="0" stop-color="#8a6a5c"/><stop offset=".5" stop-color="#efe6e4"/><stop offset="1" stop-color="#2a2626"/>
      </linearGradient>
      <linearGradient id="photo-kitchen" x1="0" y1="0" x2="0" y2="1">
        <stop offset="0" stop-color="#5a3b2c"/><stop offset=".55" stop-color="#c98e68"/><stop offset="1" stop-color="#2a2626"/>
      </linearGradient>
      <radialGradient id="photo-food">
        <stop offset="0" stop-color="#7a5238"/><stop offset=".7" stop-color="#4a3020"/><stop offset="1" stop-color="#b8403a"/>
      </radialGradient>
      <radialGradient id="photo-friends">
        <stop offset="0" stop-color="#b98468"/><stop offset=".7" stop-color="#5a3a2e"/><stop offset="1" stop-color="#e8dcd6"/>
      </radialGradient>
    </defs>
  </svg>

  <!-- Row 1: text-only covers -->
  <div class="post col-a row-1">
    <svg viewBox="0 0 440 549">
      <rect width="440" height="549" fill="var(--blush)"/>
      <circle cx="220" cy="272" r="225" fill="var(--rose)"/>
      <rect x="120" y="86" width="190" height="64" rx="32" fill="var(--forest)"/>
      <text class="head fill-white" x="215" y="135" text-anchor="middle" font-size="42" textLength="160" lengthAdjust="spacingAndGlyphs">Ten-Week</text>
      <text class="head fill-white" x="220" y="290" text-anchor="middle" font-size="150" textLength="255" lengthAdjust="spacingAndGlyphs">BRIGHT</text>
      <text class="head fill-white" x="220" y="383" text-anchor="middle" font-size="92" textLength="255" lengthAdjust="spacingAndGlyphs">MORNING</text>
      <text class="mid fill-white" x="220" y="442" text-anchor="middle" font-size="60" textLength="160" lengthAdjust="spacingAndGlyphs">Reboot</text>
    </svg>
  </div>

  <div class="post col-b row-1">
    <svg viewBox="0 0 440 549">
      <rect width="440" height="549" fill="var(--rose)"/>
      <circle cx="220" cy="272" r="235" fill="var(--blush)"/>
      <text class="light fill-forest" x="220" y="135" text-anchor="middle" font-size="48" textLength="195" lengthAdjust="spacingAndGlyphs">Done-For-You</text>
      <text class="head fill-forest" x="220" y="262" text-anchor="middle" font-size="140" textLength="230" lengthAdjust="spacingAndGlyphs">QUICK</text>
      <text class="head fill-forest" x="220" y="390" text-anchor="middle" font-size="140" textLength="290" lengthAdjust="spacingAndGlyphs">GARDEN</text>
      <text class="light fill-forest" x="220" y="450" text-anchor="middle" font-size="56" textLength="220" lengthAdjust="spacingAndGlyphs">KITCHEN MENU GUIDE</text>
    </svg>
  </div>

  <div class="post col-c row-1">
    <svg viewBox="0 0 440 549">
      <rect width="440" height="549" fill="var(--blush)"/>
      <circle cx="220" cy="272" r="235" fill="var(--rose)"/>
      <rect x="83" y="86" width="274" height="62" rx="31" fill="var(--forest)"/>
      <text class="head fill-white" x="220" y="128" text-anchor="middle" font-size="30" textLength="200" lengthAdjust="spacingAndGlyphs">Studio Habits for</text>
      <text class="head fill-white" x="220" y="290" text-anchor="middle" font-size="140" textLength="280" lengthAdjust="spacingAndGlyphs">LASTING</text>
      <text class="head fill-white" x="220" y="403" text-anchor="middle" font-size="130" textLength="310" lengthAdjust="spacingAndGlyphs">ENERGY</text>
      <rect x="92" y="418" width="256" height="36" rx="18" fill="var(--forest)"/>
      <text class="mid fill-white" x="220" y="444" text-anchor="middle" font-size="22" textLength="232" lengthAdjust="spacingAndGlyphs">Past Midlife - Zero Gym Needed</text>
    </svg>
  </div>

  <!-- Row 2 -->
  <div class="post col-a row-2">
    <svg viewBox="0 0 440 549">
      <rect width="440" height="549" fill="var(--pale)"/>
      <circle cx="130" cy="130" r="190" fill="var(--blush)"/>
      <circle cx="290" cy="45" r="52" fill="var(--rose)"/>
      <circle cx="40" cy="495" r="90" fill="var(--rose)"/>
      <rect x="400" y="145" width="40" height="70" fill="url(#dot-grid)"/>
      <rect role="img" aria-label="Coach in a white cropped sweater pointing to her midsection" x="30" y="10" width="245" height="330" rx="100" fill="url(#photo-person)"/>
      <text class="head fill-ink" x="415" y="350" text-anchor="end" font-size="46" textLength="135" lengthAdjust="spacingAndGlyphs">Ten - Week</text>
      <text class="head fill-forest" x="415" y="415" text-anchor="end" font-size="62" textLength="290" lengthAdjust="spacingAndGlyphs">BRIGHT MORNING</text>
      <text class="head fill-ink" x="415" y="468" text-anchor="end" font-size="48" textLength="125" lengthAdjust="spacingAndGlyphs">Reboot</text>
    </svg>
  </div>

  <div class="post col-b-alt row-2">
    <svg viewBox="0 0 440 549">
      <rect width="440" height="549" fill="var(--pale)"/>
      <circle cx="25" cy="180" r="50" fill="var(--rose)"/>
      <circle cx="300" cy="460" r="100" fill="var(--rose)"/>
      <rect x="105" y="5" width="70" height="42" fill="url(#dot-grid)"/>
      <rect x="410" y="340" width="30" height="70" fill="url(#dot-grid)"/>
      <circle role="img" aria-label="Overhead spread of fruit, grains and a printed meal plan sheet on wood" cx="150" cy="368" r="170" fill="url(#photo-food)"/>
      <text class="head fill-ink" x="410" y="102" text-anchor="end" font-size="48" textLength="230" lengthAdjust="spacingAndGlyphs">Done-For-You</text>
      <text class="head fill-forest" x="410" y="170" text-anchor="end" font-size="62" textLength="250" lengthAdjust="spacingAndGlyphs">QUICK GARDEN</text>
      <text class="head fill-ink" x="410" y="222" text-anchor="end" font-size="44" textLength="250" lengthAdjust="spacingAndGlyphs">Kitchen Menu Guide</text>
    </svg>
  </div>

  <div class="post col-c row-2">
    <svg viewBox="0 0 440 549">
      <rect width="440" height="549" fill="var(--pale)"/>
      <circle role="img" aria-label="Two friends sharing a whispered secret, one looking surprised" cx="290" cy="115" r="225" fill="url(#photo-friends)"/>
      <circle cx="185" cy="45" r="52" fill="var(--rose)"/>
      <circle cx="420" cy="498" r="95" fill="var(--rose)"/>
      <rect x="0" y="98" width="40" height="70" fill="url(#dot-grid)"/>
      <rect x="188" y="525" width="70" height="24" fill="url(#dot-grid)"/>
      <text class="head fill-ink" x="28" y="320" font-size="50" textLength="140" lengthAdjust="spacingAndGlyphs">Studio</text>
      <text class="head fill-ink" x="28" y="372" font-size="50" textLength="200" lengthAdjust="spacingAndGlyphs">Habits for</text>
      <text class="head fill-forest" x="28" y="438" font-size="68" textLength="295" lengthAdjust="spacingAndGlyphs">LASTING ENERGY</text>
      <text class="light fill-ink" x="28" y="472" font-size="28" textLength="292" lengthAdjust="spacingAndGlyphs">Past Midlife - Zero Gym Needed</text>
    </svg>
  </div>

  <!-- Row 3 -->
  <div class="post col-a row-3">
    <svg viewBox="0 0 440 549">
      <rect width="440" height="549" fill="var(--pale)"/>
      <circle cx="130" cy="10" r="52" fill="var(--rose)"/>
      <circle cx="430" cy="430" r="110" fill="var(--rose)"/>
      <rect x="5" y="150" width="42" height="70" fill="url(#dot-grid)"/>
      <rect x="265" y="520" width="70" height="29" fill="url(#dot-grid)"/>
      <circle role="img" aria-label="Coach in a white cropped sweater posing in a home kitchen" cx="310" cy="175" r="180" fill="url(#photo-kitchen)"/>
      <text class="head fill-ink" x="32" y="370" font-size="46" textLength="135" lengthAdjust="spacingAndGlyphs">Ten - Week</text>
      <text class="head fill-forest" x="32" y="432" font-size="62" textLength="290" lengthAdjust="spacingAndGlyphs">BRIGHT MORNING</text>
      <text class="head fill-ink" x="30" y="483" font-size="48" textLength="125" lengthAdjust="spacingAndGlyphs">Reboot</text>
    </svg>
  </div>

  <div class="post col-b-alt row-3">
    <svg viewBox="0 0 440 549">
      <rect width="440" height="549" fill="var(--pale)"/>
      <circle cx="30" cy="455" r="70" fill="var(--rose)"/>
      <rect x="355" y="0" width="70" height="42" fill="url(#dot-grid)"/>
      <rect x="0" y="290" width="30" height="70" fill="url(#dot-grid)"/>
      <circle role="img" aria-label="Table of salmon, eggs, vegetables and lentils around a meal plan notebook" cx="255" cy="440" r="190" fill="url(#photo-food)"/>
      <circle cx="410" cy="270" r="55" fill="var(--rose)"/>
      <text class="head fill-ink" x="42" y="72" font-size="48" textLength="230" lengthAdjust="spacingAndGlyphs">Done-For-You</text>
      <text class="head fill-forest" x="42" y="138" font-size="62" textLength="250" lengthAdjust="spacingAndGlyphs">QUICK GARDEN</text>
      <text class="head fill-ink" x="40" y="190" font-size="44" textLength="250" lengthAdjust="spacingAndGlyphs">Kitchen Menu Guide</text>
    </svg>
  </div>

  <div class="post col-c row-3">
    <svg viewBox="0 0 440 549">
      <rect width="440" height="549" fill="var(--pale)"/>
      <circle cx="170" cy="150" r="210" fill="var(--blush)"/>
      <circle cx="310" cy="25" r="52" fill="var(--rose)"/>
      <circle cx="55" cy="505" r="75" fill="var(--rose)"/>
      <rect x="400" y="145" width="40" height="70" fill="url(#dot-grid)"/>
      <rect role="img" aria-label="Two friends in summer tops whispering and reacting with excitement" x="20" y="15" width="255" height="320" rx="110" fill="url(#photo-friends)"/>
      <text class="head fill-ink" x="415" y="320" text-anchor="end" font-size="50" textLength="140" lengthAdjust="spacingAndGlyphs">Studio</text>
      <text class="head fill-ink" x="415" y="372" text-anchor="end" font-size="50" textLength="200" lengthAdjust="spacingAndGlyphs">Habits for</text>
      <text class="head fill-forest" x="415" y="438" text-anchor="end" font-size="68" textLength="295" lengthAdjust="spacingAndGlyphs">LASTING ENERGY</text>
      <text class="light fill-ink" x="415" y="472" text-anchor="end" font-size="28" textLength="292" lengthAdjust="spacingAndGlyphs">Past Midlife - Zero Gym Needed</text>
    </svg>
  </div>

</div>
</body>
</html>
```